Asian simmer/ cooking sauce label

We are a established small gourmet condiment company with a range of products. This is a new product range of 6 simmer sauces that we would like a label designed that represents our brand but individualizes the new range.
the label should have a upmarket authentic feel and represent Asian cooking done in a home made kitchen
There will be six varieties it they will al have the same generic design only the product details will change

Our current range can be viewed on our website www.plumbarrow.com.au

Butter Chicken has been uploaded. it is one of the products that will be used with the new label
I have uploaded a drinking chocolate label we use that has a black pattern

Target Market(s)

gourmet food shops, gifts stores

Colors

Designer to choose colors to be used in the design.

Requirements
Must have
• the labels needs to include product name. product description, ingredients, weight, nutritional panel, manufactures details and be a sized to suit jars which I will supply
• label size aprox 200mm long x 70mm high
Nice to have
• We prefer warm colours, gold, and black
• our brand name and logo
Should not have
• surprise me

```html
<!DOCTYPE html>
<html lang="en">
<head>
<meta charset="utf-8">
<title>Simmer Sauce – Butter Chicken label options</title>
<link href="https://fonts.googleapis.com/css2?family=Open+Sans:ital,wght@0,400;0,600;0,700;1,400&family=Roboto+Condensed:ital,wght@0,300;0,400;0,700;1,300&family=Sancreek&family=Playball&family=Kaushan+Script&family=Knewave&display=swap" rel="stylesheet">
<style>
  :root{
    --page:#000;
    --label:#2a2a2a;
    --label-edge:#d8d8d8;
    --gold:#c9a03a;
    --gold-soft:#a98a45;
    --gold-band:#8c6d22;
    --white:#ffffff;
    --option:#555555;
    --ink:#2a2a2a;
  }
  *{box-sizing:border-box;margin:0;padding:0}
  html,body{width:830px;height:1200px;overflow:hidden;background:var(--page)}
  .sheet{position:relative;width:830px;height:1200px}

  .option{position:absolute;left:0;width:830px;height:288px}
  .option--1{top:0}.option--2{top:288px}.option--3{top:576px}.option--4{top:864px}

  .option__name{position:absolute;left:541px;top:305px;
    font:700 18px/1 "Open Sans",sans-serif;color:var(--option);letter-spacing:.5px}

  .label{position:absolute;left:38px;top:78px;width:754px;height:205px;
    background:var(--label);border:1px solid var(--label-edge);overflow:hidden}
  .label__texture{position:absolute;inset:0;background:radial-gradient(circle at 50% 50%,#303030,#262626)}
  .label__band{position:absolute;left:0;right:0;height:13px;background:var(--gold-band);
    border-top:1px solid var(--gold);border-bottom:1px solid var(--gold)}
  .label__band--top{top:9px}
  .label__band--bottom{top:186px}

  .maker{position:absolute;left:17px;top:37px;width:102px;
    font:400 8px/9.7px "Open Sans",sans-serif;color:var(--gold)}
  .maker__net{display:inline-block;font-weight:700;font-size:6.8px;margin-bottom:2px}
  .maker p{margin-bottom:9.7px}

  .centre{position:absolute;left:192px;top:0;width:240px;height:186px;text-align:center}
  .brand{position:absolute;left:0;right:0;top:44px;display:flex;justify-content:center;align-items:center;gap:5px;
    font:700 11px/1 "Open Sans",sans-serif;color:var(--gold);letter-spacing:1px}
  .brand__mark{width:7px;height:7px;background:var(--gold)}
  .range{position:absolute;left:0;right:0;top:74px;font:400 28px/1 "Sancreek",serif;color:var(--gold)}
  .flavour{position:absolute;left:0;right:0;top:114px;height:30px;color:var(--white);white-space:nowrap}
  .flavour--script{font:400 24px/30px "Playball",cursive}
  .flavour--western{font:400 24px/30px "Sancreek",serif;letter-spacing:.5px}
  .flavour--bold{font:400 23px/30px "Kaushan Script",cursive}
  .flavour--brush{font:400 20px/30px "Knewave",cursive}
  .origin{position:absolute;left:50%;top:159px;transform:translateX(-50%);background:var(--gold);padding:1px 6px;
    font:700 5.6px/6px "Open Sans",sans-serif;color:var(--ink);white-space:nowrap;
    border-left:3px solid var(--gold-band);border-right:3px solid var(--gold-band)}

  .nutrition{position:absolute;left:503px;top:39px;width:122px;color:var(--gold)}
  .nutrition__title{font:600 10.6px/1 "Open Sans",sans-serif;white-space:nowrap;letter-spacing:-.2px}
  .nutrition__serve{margin-top:3px;font:700 6.8px/7.3px "Open Sans",sans-serif}
  .nutrition__table{width:100%;margin-top:2px;border-collapse:collapse;
    font:300 6.5px/7.9px "Roboto Condensed",sans-serif;border-top:1px solid var(--gold);border-bottom:1px solid var(--gold)}
  .nutrition__table th{font-weight:300;text-align:left;border-bottom:1px solid var(--gold)}
  .nutrition__table td:nth-child(2),.nutrition__table th:nth-child(2){padding-left:4px}
  .nutrition__ingredients{margin-top:3px;font:400 6.8px/7.9px "Open Sans",sans-serif}
  .nutrition__ingredients b{font-weight:700}

  .method{position:absolute;left:633px;top:40px;width:106px;text-align:justify;
    font:300 italic 7.4px/10.9px "Roboto Condensed",sans-serif;color:var(--gold-soft)}
</style>
</head>
<body>
<main class="sheet">

  <section class="option option--1">
    <div class="label">
      <div class="label__texture" role="img" aria-label="Dark woven pattern background"></div>
      <div class="label__band label__band--top" role="img" aria-label="Gold woven border pattern"></div>
      <div class="label__band label__band--bottom" role="img" aria-label="Gold woven border pattern"></div>
      <div class="maker">
        <p><span class="maker__net">375G NET</span><br>The Plum Barrow Kitchen<br>Old Mill Lane<br>Kestrel 2590<br>Ph/Fax (02) 5550 1234<br>www.plumbarrow.com.au</p>
        <p>HACCP Accredited<br>Made on a production line that also produces products containing eggs, soy, nuts and dairy.</p>
        <p>Refrigerate after opening.</p>
      </div>
      <div class="centre">
        <div class="brand"><span class="brand__mark"></span>HARLOW &amp; CO</div>
        <div class="range">Simmer Sauce</div>
        <div class="flavour flavour--script">Butter Chicken</div>
        <div class="origin">Proudly Australian<br>owned and made</div>
      </div>
      <div class="nutrition">
        <h2 class="nutrition__title">Nutritional Information</h2>
        <p class="nutrition__serve">Serving size &nbsp; 96g<br>Serves per pack &nbsp;4</p>
        <table class="nutrition__table">
          <tr><th></th><th>Per Serve</th><th>Per 100g</th></tr>
          <tr><td>Energy</td><td>2886kj</td><td>310kj</td></tr>
          <tr><td>Protein</td><td>1.8g</td><td>1.9g</td></tr>
          <tr><td>Fat, total</td><td>4.2g</td><td>4.6g</td></tr>
          <tr><td>–Saturated</td><td>1.3g</td><td>1.4g</td></tr>
          <tr><td>Carbohydrate</td><td>4.9g</td><td>5.3g</td></tr>
          <tr><td>–Sugar</td><td>4.6g</td><td>5.0g</td></tr>
          <tr><td>Sodium</td><td>370mg</td><td>396mg</td></tr>
        </table>
        <p class="nutrition__ingredients"><b>Ingredients:</b> tomato, onions, garlic, ginger, tamarind, almond, ghee, salt, sugar, spice. <b>Contains nuts, dairy. May contain traces of gluten.</b></p>
      </div>
      <p class="method">Heat oil and brown chicken. Add 1 jar of Butter Chicken simmer sauce and cook on medium heat for 10 minutes. Add 1 cup of cream and simmer on low heat for 5 minutes. For a low fat option replace cream with yoghurt or light evaporated milk.</p>
    </div>
    <p class="option__name">OPTION-01</p>
  </section>

  <section class="option option--2">
    <div class="label">
      <div class="label__texture" role="img" aria-label="Dark woven pattern background"></div>
      <div class="label__band label__band--top" role="img" aria-label="Gold woven border pattern"></div>
      <div class="label__band label__band--bottom" role="img" aria-label="Gold woven border pattern"></div>
      <div class="maker">
        <p><span class="maker__net">375G NET</span><br>The Plum Barrow Kitchen<br>Old Mill Lane<br>Kestrel 2590<br>Ph/Fax (02) 5550 1234<br>www.plumbarrow.com.au</p>
        <p>HACCP Accredited<br>Made on a production line that also produces products containing eggs, soy, nuts and dairy.</p>
        <p>Refrigerate after opening.</p>
      </div>
      <div class="centre">
        <div class="brand"><span class="brand__mark"></span>HARLOW &amp; CO</div>
        <div class="range">Simmer Sauce</div>
        <div class="flavour flavour--western">BUTTER CHICKEN</div>
        <div class="origin">Proudly Australian<br>owned and made</div>
      </div>
      <div class="nutrition">
        <h2 class="nutrition__title">Nutritional Information</h2>
        <p class="nutrition__serve">Serving size &nbsp; 96g<br>Serves per pack &nbsp;4</p>
        <table class="nutrition__table">
          <tr><th></th><th>Per Serve</th><th>Per 100g</th></tr>
          <tr><td>Energy</td><td>2886kj</td><td>310kj</td></tr>
          <tr><td>Protein</td><td>1.8g</td><td>1.9g</td></tr>
          <tr><td>Fat, total</td><td>4.2g</td><td>4.6g</td></tr>
          <tr><td>–Saturated</td><td>1.3g</td><td>1.4g</td></tr>
          <tr><td>Carbohydrate</td><td>4.9g</td><td>5.3g</td></tr>
          <tr><td>–Sugar</td><td>4.6g</td><td>5.0g</td></tr>
          <tr><td>Sodium</td><td>370mg</td><td>396mg</td></tr>
        </table>
        <p class="nutrition__ingredients"><b>Ingredients:</b> tomato, onions, garlic, ginger, tamarind, almond, ghee, salt, sugar, spice. <b>Contains nuts, dairy. May contain traces of gluten.</b></p>
      </div>
      <p class="method">Heat oil and brown chicken. Add 1 jar of Butter Chicken simmer sauce and cook on medium heat for 10 minutes. Add 1 cup of cream and simmer on low heat for 5 minutes. For a low fat option replace cream with yoghurt or light evaporated milk.</p>
    </div>
    <p class="option__name">OPTION-02</p>
  </section>

  <section class="option option--3">
    <div class="label">
      <div class="label__texture" role="img" aria-label="Dark woven pattern background"></div>
      <div class="label__band label__band--top" role="img" aria-label="Gold woven border pattern"></div>
      <div class="label__band label__band--bottom" role="img" aria-label="Gold woven border pattern"></div>
      <div class="maker">
        <p><span class="maker__net">375G NET</span><br>The Plum Barrow Kitchen<br>Old Mill Lane<br>Kestrel 2590<br>Ph/Fax (02) 5550 1234<br>www.plumbarrow.com.au</p>
        <p>HACCP Accredited<br>Made on a production line that also produces products containing eggs, soy, nuts and dairy.</p>
        <p>Refrigerate after opening.</p>
      </div>
      <div class="centre">
        <div class="brand"><span class="brand__mark"></span>HARLOW &amp; CO</div>
        <div class="range">Simmer Sauce</div>
        <div class="flavour flavour--bold">Butter Chicken</div>
        <div class="origin">Proudly Australian<br>owned and made</div>
      </div>
      <div class="nutrition">
        <h2 class="nutrition__title">Nutritional Information</h2>
        <p class="nutrition__serve">Serving size &nbsp; 96g<br>Serves per pack &nbsp;4</p>
        <table class="nutrition__table">
          <tr><th></th><th>Per Serve</th><th>Per 100g</th></tr>
          <tr><td>Energy</td><td>2886kj</td><td>310kj</td></tr>
          <tr><td>Protein</td><td>1.8g</td><td>1.9g</td></tr>
          <tr><td>Fat, total</td><td>4.2g</td><td>4.6g</td></tr>
          <tr><td>–Saturated</td><td>1.3g</td><td>1.4g</td></tr>
          <tr><td>Carbohydrate</td><td>4.9g</td><td>5.3g</td></tr>
          <tr><td>–Sugar</td><td>4.6g</td><td>5.0g</td></tr>
          <tr><td>Sodium</td><td>370mg</td><td>396mg</td></tr>
        </table>
        <p class="nutrition__ingredients"><b>Ingredients:</b> tomato, onions, garlic, ginger, tamarind, almond, ghee, salt, sugar, spice. <b>Contains nuts, dairy. May contain traces of gluten.</b></p>
      </div>
      <p class="method">Heat oil and brown chicken. Add 1 jar of Butter Chicken simmer sauce and cook on medium heat for 10 minutes. Add 1 cup of cream and simmer on low heat for 5 minutes. For a low fat option replace cream with yoghurt or light evaporated milk.</p>
    </div>
    <p class="option__name">OPTION-03</p>
  </section>

  <section class="option option--4">
    <div class="label">
      <div class="label__texture" role="img" aria-label="Dark woven pattern background"></div>
      <div class="label__band label__band--top" role="img" aria-label="Gold woven border pattern"></div>
      <div class="label__band label__band--bottom" role="img" aria-label="Gold woven border pattern"></div>
      <div class="maker">
        <p><span class="maker__net">375G NET</span><br>The Plum Barrow Kitchen<br>Old Mill Lane<br>Kestrel 2590<br>Ph/Fax (02) 5550 1234<br>www.plumbarrow.com.au</p>
        <p>HACCP Accredited<br>Made on a production line that also produces products containing eggs, soy, nuts and dairy.</p>
        <p>Refrigerate after opening.</p>
      </div>
      <div class="centre">
        <div class="brand"><span class="brand__mark"></span>HARLOW &amp; CO</div>
        <div class="range">Simmer Sauce</div>
        <div class="flavour flavour--brush">BUTTER CHICKEN</div>
        <div class="origin">Proudly Australian<br>owned and made</div>
      </div>
      <div class="nutrition">
        <h2 class="nutrition__title">Nutritional Information</h2>
        <p class="nutrition__serve">Serving size &nbsp; 96g<br>Serves per pack &nbsp;4</p>
        <table class="nutrition__table">
          <tr><th></th><th>Per Serve</th><th>Per 100g</th></tr>
          <tr><td>Energy</td><td>2886kj</td><td>310kj</td></tr>
          <tr><td>Protein</td><td>1.8g</td><td>1.9g</td></tr>
          <tr><td>Fat, total</td><td>4.2g</td><td>4.6g</td></tr>
          <tr><td>–Saturated</td><td>1.3g</td><td>1.4g</td></tr>
          <tr><td>Carbohydrate</td><td>4.9g</td><td>5.3g</td></tr>
          <tr><td>–Sugar</td><td>4.6g</td><td>5.0g</td></tr>
          <tr><td>Sodium</td><td>370mg</td><td>396mg</td></tr>
        </table>
        <p class="nutrition__ingredients"><b>Ingredients:</b> tomato, onions, garlic, ginger, tamarind, almond, ghee, salt, sugar, spice. <b>Contains nuts, dairy. May contain traces of gluten.</b></p>
      </div>
      <p class="method">Heat oil and brown chicken. Add 1 jar of Butter Chicken simmer sauce and cook on medium heat for 10 minutes. Add 1 cup of cream and simmer on low heat for 5 minutes. For a low fat option replace cream with yoghurt or light evaporated milk.</p>
    </div>
    <p class="option__name">OPTION-04</p>
  </section>

</main>
</body>
</html>
```